Web Developer Needs a Business Card Design

I need a personal business card design that represents me as a web developer for potential employers. I would like the background to be a dark color on the front for contrast with my logo and name. The back will have all my information along with a smaller version of the logo. I want something with a modern look and feel, not too conservative. This will be used for potential employers and freelance work.

Industry/Entity Type

Business

Contact Information for Business Card

Front should have my logo and name. The back should have all my personal information which would include: name: Tom Varulek, phone: 570-614-3098, email: tomvarulek@quillbox.net, website url: www.tomvarulek.net, logo, web developer.

Font styles to use
Sans Serif

Requirements
Must have
• Must include my logo. The color palette base color will be the logo color.

```html
<!DOCTYPE html>
<html lang="en">
<head>
<meta charset="utf-8">
<title>Tom Varulek – Business Card</title>
<link href="https://fonts.googleapis.com/css2?family=Source+Sans+3:wght@400;600&display=swap" rel="stylesheet">
<style>
  :root {
    --stage: #000000;
    --card-light: #f3f3f3;
    --card-mint: #52e5c4;
    --mint-deep: #6cc9b4;
    --mint-text: #3cc9a8;
    --ink: #1a1a1a;
    --white: #ffffff;
  }
  html, body {
    margin: 0;
    padding: 0;
    width: 1200px;
    height: 900px;
    overflow: hidden;
    background: var(--stage);
    font-family: "Source Sans 3", sans-serif;
  }
  .stage { position: relative; width: 1200px; height: 900px; }

  .card { position: absolute; top: 200px; width: 310px; height: 502px; box-sizing: border-box; }
  .card--back {
    left: 265px;
    background: var(--card-light);
    border-radius: 70px 0 70px 0;
  }
  .card--front {
    left: 641px;
    width: 308px;
    background: var(--card-mint);
    border-radius: 0 70px 0 70px;
  }

  .mark {
    position: absolute;
    display: flex;
    align-items: center;
    justify-content: center;
    border-radius: 50%;
    box-sizing: border-box;
    font-weight: 600;
    letter-spacing: -1px;
  }
  .mark--small {
    left: 142px; top: 38px;
    width: 132px; height: 132px;
    border: 7px solid var(--mint-deep);
    color: var(--mint-deep);
    font-size: 54px;
  }
  .mark--large {
    left: 58px; top: 199px;
    width: 188px; height: 188px;
    border: 10px solid var(--white);
    color: var(--white);
    font-size: 78px;
  }

  .identity { position: absolute; left: 24px; top: 344px; }
  .identity__name { margin: 0; font-size: 19px; font-weight: 600; color: var(--mint-text); line-height: 1.1; }
  .identity__role { margin: 2px 0 0; font-size: 14px; color: var(--ink); }

  .contacts { position: absolute; left: 24px; top: 408px; margin: 0; padding: 0; list-style: none; }
  .contacts li { display: flex; align-items: center; height: 21px; font-size: 14px; color: var(--ink); }
  .contacts svg { width: 10px; height: 10px; margin-right: 7px; fill: var(--mint-text); }

  .front-name {
    position: absolute; left: 0; right: 0; top: 418px;
    margin: 0; text-align: center;
    font-size: 27px; font-weight: 600; color: var(--white);
  }
</style>
</head>
<body>
<main class="stage">
  <section class="card card--back">
    <div class="mark mark--small">tv</div>
    <div class="identity">
      <h1 class="identity__name">Tom Varulek</h1>
      <p class="identity__role">Front-End Developer</p>
    </div>
    <ul class="contacts">
      <li><svg viewBox="0 0 10 10"><path d="M2 0.5 L3.8 2.6 L2.8 3.8 Q4 6.2 6.2 7.2 L7.4 6.2 L9.5 8 L8.4 9.5 Q4.5 9.4 1.5 6 Q0 3.5 0.5 1.6 Z"/></svg>570-614-3098</li>
      <li><svg viewBox="0 0 10 10"><path d="M0 2 H10 V8 H0 Z M0.6 2.4 L5 5.6 L9.4 2.4" stroke="#f3f3f3" stroke-width="0.8"/></svg>tomvarulek@quillbox.net</li>
      <li><svg viewBox="0 0 10 10"><path d="M4 6 L6 4" stroke="#3cc9a8" stroke-width="1.2" fill="none"/><path d="M3.5 4.5 L1.5 6.5 Q0.5 8.5 2.5 8.5 L4.5 6.5 M6.5 5.5 L8.5 3.5 Q9.5 1.5 7.5 1.5 L5.5 3.5" stroke="#3cc9a8" stroke-width="1.2" fill="none"/></svg>www.tomvarulek.net</li>
    </ul>
  </section>

  <section class="card card--front">
    <div class="mark mark--large">tv</div>
    <h2 class="front-name">Tom Varulek</h2>
  </section>
</main>
</body>
</html>
```